Brightwave Reach - Business Card

We need a business card for a Social Media Marketing company that specializes in online marketing for small businesses in Canada using common Social Media platforms such as Pixlora, Chatterly, Blinkpost & Quibber.

I have uploaded a copy of our logo which I would like utilized in the business card. We would like the business card to be modern yet classy design.

Our website is www.brightwavereach.ca

Industry/Entity Type

Marketing

Contact Information for Business Card

Email: info@brightwavereach.ca
Website: www.brightwavereach.ca
Telephone: 604-555-0193

Colors

Designer to choose colors to be used in the design.

Requirements
Must have
• Social Media icons on reverse
• Please add some designs with color.

```html
<!DOCTYPE html>
<html lang="en">
<head>
<meta charset="utf-8">
<title>Brightwave Reach – Business Card</title>
<link rel="stylesheet" href="https://fonts.googleapis.com/css2?family=Teko:wght@500;600&display=swap">
<style>
  :root {
    --backdrop: #1c1d1f;
    --card: #4a4e52;
    --card-edge: #42464a;
    --ink: #f2f2f2;
    --ink-soft: #d9dadb;
    --accent: #e2483d;
  }
  * { margin: 0; padding: 0; box-sizing: border-box; }
  html, body {
    width: 1200px;
    height: 1000px;
    overflow: hidden;
    background: var(--backdrop);
  }
  .canvas {
    position: relative;
    width: 1200px;
    height: 1000px;
    font-family: "Teko", "Arial Narrow", sans-serif;
    color: var(--ink);
  }
  .card {
    position: absolute;
    width: 620px;
    height: 354px;
    border-radius: 26px;
    background: linear-gradient(160deg, var(--card) 0%, var(--card-edge) 100%);
    box-shadow: 0 14px 34px rgba(0, 0, 0, 0.45);
  }
  .card--front { left: 100px; top: 110px; }
  .card--back  { left: 480px; top: 536px; }

  .brand {
    display: flex;
    align-items: center;
    gap: 10px;
    font-weight: 600;
    text-transform: uppercase;
    letter-spacing: 1px;
    line-height: 1;
    color: var(--ink);
  }
  .brand__square {
    flex: none;
    width: 14px;
    height: 14px;
    background: var(--accent);
  }
  .card--front .brand {
    position: absolute;
    left: 0; right: 0;
    top: 118px;
    justify-content: center;
    font-size: 52px;
  }
  .social-list {
    position: absolute;
    left: 0; right: 0;
    top: 232px;
    display: flex;
    justify-content: center;
    gap: 18px;
    list-style: none;
    font-weight: 500;
    font-size: 16px;
    line-height: 1;
    letter-spacing: 1px;
    text-transform: uppercase;
    color: var(--ink-soft);
  }
  .social-list__item {
    display: flex;
    align-items: center;
    gap: 6px;
  }
  .social-list__dot {
    flex: none;
    width: 9px;
    height: 9px;
    border-radius: 50%;
    background: var(--accent);
  }
  .card--back .brand {
    position: absolute;
    right: 44px;
    top: 48px;
    font-size: 26px;
    gap: 7px;
  }
  .card--back .brand__square { width: 9px; height: 9px; }

  .person {
    position: absolute;
    left: 48px;
    top: 118px;
    text-transform: uppercase;
    line-height: 1;
  }
  .person__name {
    font-weight: 600;
    font-size: 34px;
    letter-spacing: 2px;
  }
  .person__role {
    margin-top: 6px;
    font-weight: 500;
    font-size: 16px;
    letter-spacing: 1.5px;
    color: var(--ink-soft);
  }
  .contact {
    position: absolute;
    left: 48px;
    bottom: 34px;
    list-style: none;
    font-weight: 500;
    font-size: 17px;
    letter-spacing: 1.5px;
    line-height: 1.35;
    text-transform: uppercase;
    color: var(--ink-soft);
  }
  .contact__label { color: var(--accent); }
</style>
</head>
<body>
<main class="canvas">
  <section class="card card--front" aria-label="Card front">
    <div class="brand"><span class="brand__square"></span>Brightwave Reach</div>
    <ul class="social-list">
      <li class="social-list__item"><span class="social-list__dot"></span>Chatterly</li>
      <li class="social-list__item"><span class="social-list__dot"></span>Quibber</li>
      <li class="social-list__item"><span class="social-list__dot"></span>Pixlora</li>
      <li class="social-list__item"><span class="social-list__dot"></span>Blinkpost</li>
    </ul>
  </section>

  <section class="card card--back" aria-label="Card back">
    <div class="brand"><span class="brand__square"></span>Brightwave Reach</div>
    <div class="person">
      <p class="person__name">Daniel Porter</p>
      <p class="person__role">President</p>
    </div>
    <ul class="contact">
      <li><span class="contact__label">P:</span> 604-555-0193</li>
      <li><span class="contact__label">E:</span> info@brightwavereach.ca</li>
      <li><span class="contact__label">W:</span> brightwavereach.ca</li>
    </ul>
  </section>
</main>
</body>
</html>
```